International Clinical Software Company needs a new business card design

We are looking for a new business card design for our company that has recently expanded into the UK market, making us a multinational company.
After having rebranded our website and produced a new style guide, we are looking for a business card that is creative and attention grabbing, while being consistent with the style and colour scheme used on the new website, www.plumvora.example
We produce care management technology for the aged care market, but the main aspect we aim to communicate is the human element of our software, and the way it assists in providing better care for aged people, and stronger relationships between aged people and the staff that care for them.
Our current business card is a dark green with gold text, which makes the text quite difficult to read, not very aesthetically appealing and the colour scheme looks quite dated.
We would like something fresh and modern, that can still be colourful but doesn't use large blocks of dark colour, and uses the colours within our logo.
Something tying in with the leaves that are used in our logo could work quite nicely, along with the Autumn/Fall colours of soft greens, yellows and reds (also in our existing logo). However also happy to look at fresh, completely out of the box ideas we may not have yet considered.
Target Market(s)
The people that receive this business card work in the aged card or health industry and are either corporate/management level staff or clinical (Registered Nurses, care workers etc.)
Industry/Entity Type
Health Product
Contact Information for Business Card
Company Name - BrindlewayCare
Company locations: United Kingdom, Australia, New Zealand
Staff Details:
Staff name: Derek Mallow
Staff job title: Executive Chairman
Staff email: d.mallow@plumvora.example
Office phone number: 01742 918576
Font styles to use
Other font styles liked:
- Calibri
Requirements
Must have
- Must include the BrindlewayCare brand name in it's current font
- Must include logo (3 leaves in gold circle)
- Must include Business Card Details
Nice to have
- Elements of gold
- White space
- Something autumn themed but not too cliched
Should not have
- No blue - used by a major competitor and we would like to differentiate from them
- Large blocks of dark green colour (the green that appears in our leaves on the logo on our current business card is the background colour and it is far too dark)

```html
<!DOCTYPE html>
<html lang="en">
<head>
<meta charset="utf-8">
<title>BrindlewayCare – Business Card</title>
<link href="https://fonts.googleapis.com/css2?family=Open+Sans:wght@400;600;700&display=swap" rel="stylesheet">
<style>
  :root {
    --page-bg: #e9e9e7;
    --card-bg: #f7f6f3;
    --card-edge: #d8d4cb;
    --gold: #8a7346;
    --gold-band: #95804f;
    --band-text: #efe8d8;
    --crimson: #8c1a2b;
    --ink: #5a4f3c;
    --icon: #4b5a2e;
  }
  html, body {
    margin: 0;
    padding: 0;
    width: 1200px;
    height: 970px;
    overflow: hidden;
    background: var(--page-bg);
    font-family: "Open Sans", Calibri, sans-serif;
  }
  .canvas {
    position: relative;
    width: 1200px;
    height: 970px;
  }
  .business-card {
    position: absolute;
    left: 100px;
    top: 207px;
    width: 1000px;
    height: 556px;
    background: var(--card-bg);
    border: 1px solid var(--card-edge);
    border-radius: 26px;
    overflow: hidden;
    box-shadow: 0 10px 30px rgba(0,0,0,0.12);
  }
  .brand-mark {
    position: absolute;
    left: 50%;
    top: 70px;
    width: 112px;
    height: 112px;
    margin-left: -56px;
    box-sizing: border-box;
    border: 5px solid var(--gold);
    border-radius: 50%;
  }
  .brand-name {
    position: absolute;
    left: 0;
    right: 0;
    top: 212px;
    margin: 0;
    text-align: center;
    font-size: 62px;
    font-weight: 400;
    color: var(--gold);
    letter-spacing: 1px;
  }
  .person-name {
    position: absolute;
    left: 0; right: 0;
    top: 352px;
    margin: 0;
    text-align: center;
    font-size: 29px;
    font-weight: 700;
    color: var(--crimson);
    letter-spacing: 0.5px;
  }
  .person-title {
    position: absolute;
    left: 0; right: 0;
    top: 395px;
    margin: 0;
    text-align: center;
    font-size: 21px;
    color: var(--ink);
  }
  .contact-row {
    position: absolute;
    left: 0; right: 0;
    top: 452px;
    display: flex;
    justify-content: center;
    align-items: center;
    gap: 40px;
    font-size: 22px;
    color: var(--ink);
  }
  .contact-item {
    display: flex;
    align-items: center;
    gap: 12px;
  }
  .phone-number { letter-spacing: 3px; }
  .contact-icon { width: 30px; height: 30px; }
  .locations-band {
    position: absolute;
    left: 0; right: 0; bottom: 0;
    height: 50px;
    background: var(--gold-band);
    color: var(--band-text);
    font-size: 20px;
    letter-spacing: 3px;
    display: flex;
    align-items: center;
    justify-content: center;
  }
</style>
</head>
<body>
<div class="canvas">
  <section class="business-card">
    <div class="brand-mark"></div>
    <h1 class="brand-name">BrindlewayCare</h1>

    <h2 class="person-name">DEREK MALLOW</h2>
    <p class="person-title">Executive Chairman</p>

    <div class="contact-row">
      <div class="contact-item">
        <span class="phone-number">01742 918576</span>
        <svg class="contact-icon" viewBox="0 0 30 30" aria-hidden="true">
          <circle cx="15" cy="15" r="13" fill="none" stroke="var(--icon)" stroke-width="2"/>
          <path d="M10.5 8.5c1-.8 2-.6 2.5.3l1.1 2.2c.4.8.1 1.5-.6 2l-.8.6c.7 1.6 1.9 2.8 3.5 3.5l.6-.8c.5-.7 1.2-1 2-.6l2.2 1.1c.9.5 1.1 1.5.3 2.5-1 1.2-2.6 1.6-4.2.9-3.4-1.4-6.1-4.1-7.5-7.5-.7-1.6-.3-3.2.9-4.2z" fill="var(--icon)"/>
        </svg>
      </div>
      <div class="contact-item">
        <svg class="contact-icon" viewBox="0 0 30 30" aria-hidden="true">
          <circle cx="15" cy="15" r="13" fill="none" stroke="var(--icon)" stroke-width="2"/>
          <rect x="8" y="10" width="14" height="10" rx="1" fill="var(--icon)"/>
          <path d="M8.5 10.8 15 15.6l6.5-4.8" fill="none" stroke="var(--card-bg)" stroke-width="1.4"/>
        </svg>
        <span class="email">d.mallow@plumvora.example</span>
      </div>
    </div>

    <footer class="locations-band">United Kingdom, Australia, New Zealand</footer>
  </section>
</div>
</body>
</html>
```